Pipe Repair Clamps

A double side A4 showing our pipe repair clamps for stopping leaking pipes within seconds. For water , sewage companies, hotels, malls, airports, hosptals, facilities management companies and district cooling companies. Reverse side will show a size chart. Examples of product uploaded

```html
<!DOCTYPE html>
<html lang="en">
<head>
<meta charset="utf-8">
<title>Pipe Repair Clamps – Size Chart</title>
<link href="https://fonts.googleapis.com/css2?family=Arimo:wght@400;700&family=Roboto:wght@400;500;700&family=Roboto+Condensed:wght@400&display=swap" rel="stylesheet">
<style>
:root{
  --orange:#c8622f;
  --cta-orange:#d4822e;
  --panel-blue:#4a7cc4;
  --black:#000;
  --white:#fff;
  --teal:#1aa0c8;
  --ink:#222;
  --rule-green:#2e8a5e;
  --stripe:rgba(214,236,226,.75);
  --row:rgba(255,255,255,.6);
}
*{margin:0;padding:0;box-sizing:border-box}
html,body{width:927px;height:1200px;overflow:hidden}
body{position:relative;font-family:"Roboto",Arial,sans-serif;
  background:linear-gradient(180deg,#ffffff 0%,#eaf6fc 25%,#cbe9f7 50%,#b9e0f3 64%,#d4ecf7 72%,#eef7fb 78%);}
.skyline{position:absolute;left:0;top:780px;width:927px;height:240px;
  background:linear-gradient(180deg,rgba(238,247,251,0) 0%,#9fb8c8 30%,#7d98ab 55%,#3f8fb5 78%,#2f7fa8 100%);}
.band{position:absolute;left:0;top:1020px;width:927px;height:8px;background:var(--panel-blue)}
.footer{position:absolute;left:0;top:1028px;width:624px;height:172px;background:var(--white);text-align:center}
.call{position:absolute;top:20px;left:0;width:624px;font-size:30px;font-weight:400;color:var(--ink)}
.phone{position:absolute;top:54px;left:0;width:624px;font-size:74px;font-weight:700;color:var(--cta-orange);line-height:1}
.web{position:absolute;top:122px;left:0;width:624px;font-size:21px;font-weight:500;letter-spacing:6px;color:var(--teal)}

.chart{position:absolute;left:44px;top:68px;width:534px;border-collapse:collapse;table-layout:fixed;
  font-family:"Roboto Condensed",Arial,sans-serif;font-size:8px;color:var(--ink);text-align:center}
.chart th{background:var(--orange);color:var(--white);font-weight:400;font-size:7.5px;letter-spacing:.3px}
.chart thead tr:first-child th{height:30px;border-bottom:1px solid rgba(255,255,255,.6)}
.chart thead tr:last-child th{height:29px;line-height:1.5}
.chart th+th{border-left:1px solid rgba(255,255,255,.6)}
.chart td{height:17.3px;background:var(--row)}
.chart tbody tr:nth-child(even) td{background:var(--stripe)}
.chart tbody tr:last-child td{border-bottom:2px solid var(--rule-green)}
.note{position:absolute;left:52px;top:746px;font-family:Arial,sans-serif;font-size:7px;color:var(--ink)}

.sidebar{position:absolute;left:624px;top:0;width:268px;height:1096px;background:var(--black)}
.brand{position:absolute;left:0;top:0;width:268px;height:304px;
  background:radial-gradient(circle at 60% 40%,#6fa4cf 0%,#2f5f8c 45%,#0d2238 100%);
  display:flex;flex-direction:column;align-items:center;justify-content:center;gap:14px}
.brand-dot{width:84px;height:84px;border-radius:50%;background:var(--cta-orange)}
.brand-name{font-family:"Arimo",Arial,sans-serif;font-weight:700;font-size:24px;color:var(--white);text-align:center;line-height:1.15}
.tab{position:absolute;left:-2px;width:272px;background:var(--panel-blue);color:var(--white);
  font-family:"Arimo",Arial,sans-serif;font-weight:700;font-size:39px;text-align:center;
  display:flex;align-items:center;justify-content:center;line-height:1.3}
.tab-capping{top:305px;height:77px}
.tab-fittings{top:390px;height:90px}
.tab-flow{top:488px;height:124px}
.about{position:absolute;left:18px;top:634px;width:240px;color:var(--white);font-size:17.5px;line-height:21.8px}
.about p+p{margin-top:21.8px}
.accent{position:absolute;left:624px;top:1124px;width:268px;height:8px;background:var(--cta-orange)}
.base{position:absolute;left:624px;top:1134px;width:268px;height:66px;background:var(--black)}
</style>
</head>
<body>
<div class="skyline" role="img" aria-label="Photograph of a coastal city skyline with towers over blue water"></div>

<table class="chart">
  <colgroup>
    <col style="width:42px"><col style="width:82px"><col style="width:40px"><col style="width:43px">
    <col style="width:32px"><col style="width:29px"><col style="width:32px"><col style="width:84px">
    <col style="width:68px"><col style="width:38px"><col style="width:44px">
  </colgroup>
  <thead>
    <tr><th>Pipe O.D.</th><th>O.D.Range</th><th>Ship</th><th>Industry</th><th colspan="5">Dimensions</th><th>Screws</th><th>Screw<br>Torque</th></tr>
    <tr><th>OD<br>(mm)</th><th>ODmin–ODmax<br>(mm)</th><th>PN<br>(mm)</th><th>WP<br>(bar)</th><th>C<br>(mm)</th><th>l1<br>(mm)</th><th>l2<br>(mm)</th><th>D<br>(mm)</th><th>H<br>(mm)</th><th>M</th><th>Nm</th></tr>
  </thead>
  <tbody>
    <tr><td>21.7</td><td>21-23</td><td>16</td><td>32</td><td>3</td><td>57</td><td>–</td><td>35</td><td>50</td><td>6</td><td>15</td></tr>
    <tr><td>25</td><td>24.5-25.5</td><td>16</td><td>32</td><td>3</td><td>57</td><td>–</td><td>50</td><td>70</td><td>6</td><td>15</td></tr>
    <tr><td>27.2</td><td>26-28</td><td>16</td><td>32</td><td>3</td><td>57</td><td>–</td><td>50</td><td>70</td><td>6</td><td>15</td></tr>
    <tr><td>32</td><td>31.5-32.5</td><td>16</td><td>32</td><td>3</td><td>57</td><td>–</td><td>55</td><td>75</td><td>6</td><td>15</td></tr>
    <tr><td>34</td><td>33-35</td><td>16</td><td>32</td><td>3</td><td>57</td><td>–</td><td>55</td><td>75</td><td>6</td><td>15</td></tr>
    <tr><td>40</td><td>39.5-41.5</td><td>16</td><td>32</td><td>5</td><td>57</td><td>–</td><td>55</td><td>75</td><td>6</td><td>15</td></tr>
    <tr><td>42</td><td>42-44</td><td>16</td><td>32</td><td>5</td><td>57</td><td>–</td><td>65</td><td>85</td><td>6</td><td>15</td></tr>
    <tr><td>44.5</td><td>44-45.1</td><td>16</td><td>32</td><td>5</td><td>57</td><td>–</td><td>65</td><td>85</td><td>6</td><td>15</td></tr>
    <tr><td>48.6</td><td>47-49</td><td>16</td><td>32</td><td>5</td><td>57</td><td>100</td><td>70</td><td>90</td><td>6</td><td>15</td></tr>
    <tr><td>54</td><td>53.3-54.6</td><td>16</td><td>32</td><td>5</td><td>57</td><td>100</td><td>70</td><td>90</td><td>8</td><td>30</td></tr>
    <tr><td>57</td><td>56.3-57.7</td><td>16</td><td>32</td><td>5</td><td>57</td><td>100</td><td>50</td><td>100</td><td>8</td><td>30</td></tr>
    <tr><td>60.3</td><td>59-62</td><td>16</td><td>32</td><td>5</td><td>80</td><td>139</td><td>85</td><td>105</td><td>8</td><td>30</td></tr>
    <tr><td>63</td><td>62.2-63.9</td><td>16</td><td>32</td><td>5</td><td>80</td><td>139</td><td>85</td><td>105</td><td>8</td><td>30</td></tr>
    <tr><td>76.1</td><td>75-78</td><td>14</td><td>28</td><td>5</td><td>80</td><td>139</td><td>100</td><td>120</td><td>8</td><td>30</td></tr>
    <tr><td>79.9</td><td>78.8-80.8</td><td>14</td><td>28</td><td>5</td><td>80</td><td>139</td><td>100</td><td>120</td><td>8</td><td>30</td></tr>
    <tr><td>88.9</td><td>88-92</td><td>14</td><td>28</td><td>5</td><td>107</td><td>203</td><td>110</td><td>130</td><td>10</td><td>50</td></tr>
    <tr><td>108</td><td>106-110</td><td>14</td><td>28</td><td>5</td><td>107</td><td>203</td><td>130</td><td>150</td><td>10</td><td>50</td></tr>
    <tr><td>110</td><td>108.9-111.2</td><td>14</td><td>28</td><td>5</td><td>107</td><td>203</td><td>130</td><td>150</td><td>10</td><td>50</td></tr>
    <tr><td>114.3</td><td>112-116</td><td>14</td><td>28</td><td>5</td><td>107</td><td>203</td><td>135</td><td>155</td><td>10</td><td>50</td></tr>
    <tr><td>118</td><td>116.6-119.2</td><td>14</td><td>28</td><td>5</td><td>107</td><td>203</td><td>140</td><td>160</td><td>10</td><td>50</td></tr>
    <tr><td>125</td><td>123.6-126.5</td><td>14</td><td>28</td><td>5</td><td>107</td><td>203</td><td>150</td><td>185</td><td>10</td><td>50</td></tr>
    <tr><td>133</td><td>131.5-134.4</td><td>14</td><td>28</td><td>5</td><td>107</td><td>203</td><td>160</td><td>190</td><td>10</td><td>50</td></tr>
    <tr><td>140</td><td>137-143</td><td>14</td><td>28</td><td>5</td><td>116</td><td>203</td><td>165</td><td>195</td><td>12</td><td>80</td></tr>
    <tr><td>159</td><td>157-161</td><td>12</td><td>24</td><td>10</td><td>116</td><td>203</td><td>185</td><td>215</td><td>12</td><td>80</td></tr>
    <tr><td>165.2</td><td>163.3-166.7</td><td>12</td><td>24</td><td>10</td><td>116</td><td>203</td><td>190</td><td>210</td><td>12</td><td>80</td></tr>
    <tr><td>168</td><td>166-170</td><td>12</td><td>24</td><td>10</td><td>116</td><td>203</td><td>195</td><td>225</td><td>12</td><td>80</td></tr>
    <tr><td>170</td><td>168.2-171.9</td><td>12</td><td>24</td><td>10</td><td>116</td><td>203</td><td>195</td><td>225</td><td>14</td><td>100</td></tr>
    <tr><td>200</td><td>198.2-201.5</td><td>8</td><td>16</td><td>10</td><td>116</td><td>203</td><td>240</td><td>270</td><td>14</td><td>100</td></tr>
    <tr><td>219</td><td>217-221</td><td>8</td><td>16</td><td>10</td><td>155</td><td>255</td><td>250</td><td>280</td><td>14</td><td>100</td></tr>
    <tr><td>250</td><td>250-254</td><td>8</td><td>16</td><td>10</td><td>155</td><td>255</td><td>285</td><td>315</td><td>14</td><td>100</td></tr>
    <tr><td>273</td><td>271-275</td><td>8</td><td>16</td><td>10</td><td>155</td><td>255</td><td>305</td><td>335</td><td>14</td><td>100</td></tr>
    <tr><td>315</td><td>313-317</td><td>7</td><td>14</td><td>10</td><td>155</td><td>255</td><td>340</td><td>375</td><td>14</td><td>100</td></tr>
    <tr><td>325</td><td>323-327</td><td>7</td><td>14</td><td>10</td><td>155</td><td>255</td><td>360</td><td>390</td><td>14</td><td>100</td></tr>
    <tr><td>355.6</td><td>354-358</td><td>7</td><td>14</td><td>10</td><td>155</td><td>255</td><td>385</td><td>420</td><td>14</td><td>100</td></tr>
    <tr><td>377</td><td>375-379</td><td>7</td><td>14</td><td>10</td><td>155</td><td>255</td><td>410</td><td>440</td><td>14</td><td>100</td></tr>
  </tbody>
</table>
<p class="note">Some sizes and lengths not listed are avaliable upon request.</p>

<div class="band"></div>
<div class="footer">
  <p class="call">CALL US NOW</p>
  <p class="phone">123 456 7890</p>
  <p class="web">WWW.YOURWEBSITE.COM</p>
</div>

<aside class="sidebar">
  <div class="brand" role="img" aria-label="Company name over a photograph of splashing blue water">
    <span class="brand-dot"></span>
    <span class="brand-name">Northline<br>Pipe Fittings</span>
  </div>
  <div class="tab tab-capping">CAPPING</div>
  <div class="tab tab-fittings">FITTINGS</div>
  <div class="tab tab-flow">FLOW<br>CONTROL</div>
  <div class="about">
    <p>The company’s focus is on the civil engineering, water and sewerage treatment and gas industries, although some of the products offered are specifically for the building services and fire protection industries.</p>
    <p>We represent some of the world’s best-known manu­facturers and stock a full range of products at our premises in Kilbrook. All of our products are fully tested and approved to National and International standards and come with a full after sales service from both ourselves, and our suppliers.</p>
  </div>
</aside>
<div class="accent"></div>
<div class="base"></div>
</body>
</html>
```